Hollow Marigold Distillery

I need a label designed for my small distillery. I’d like it to have a rose, and the name hollow marigold in script writing. I need the graphic to fit a standard gin bottle and I’ll need to be able to edit it depending on alcohol, warning and descriptions. I want it to look elegant and attractive, but slightly daring too. It’s a 700ml oslo bottle
Target Market(s)
Bespoke gin and vodka drinkers
Industry/Entity Type
Beverage
Font styles to use
Script
Other font styles liked:
- Something easy to read
Requirements
Must have
- Room for me to add and remove text depending on the drink
Nice to have
- Hollow marigold in script, slight colour on the rose and black writing

```html
<!DOCTYPE html>
<html lang="en">
<head>
<meta charset="utf-8">
<title>Hollow Marigold Distillery – Gin Label</title>
<link rel="stylesheet" href="https://fonts.googleapis.com/css2?family=Oswald:wght@600&family=Josefin+Sans:wght@600&display=swap">
<style>
  :root {
    --backdrop: #e6e6e6;
    --paper: #f6f6f4;
    --ink: #3a3a3a;
    --ink-dark: #2a2a2a;
    --accent: #c8323a;
    --rule: #8a8a8a;
    --art-tone: #d9d7d4;
  }
  html, body {
    margin: 0;
    padding: 0;
    width: 960px;
    height: 1200px;
    overflow: hidden;
    background: var(--backdrop);
  }
  .label {
    position: absolute;
    left: 70px;
    top: 72px;
    width: 820px;
    height: 1056px;
    background: var(--paper);
    box-sizing: border-box;
  }
  .label__frame {
    position: absolute;
    inset: 14px 14px 16px 14px;
    border: 1px solid var(--rule);
  }
  .label__frame::after {
    content: "";
    position: absolute;
    inset: 4px;
    border: 1px solid var(--rule);
  }
  .botanical {
    position: absolute;
    background: linear-gradient(90deg, var(--art-tone), #ecebe9);
    border-radius: 60px;
  }
  .botanical--top { left: 243px; top: 92px; width: 324px; height: 118px; }
  .botanical--bottom { left: 259px; top: 772px; width: 332px; height: 118px; }
  .arc-tagline {
    position: absolute;
    left: 160px;
    top: 262px;
    width: 500px;
    height: 120px;
  }
  .arc-tagline text {
    font-family: "Josefin Sans", sans-serif;
    font-weight: 600;
    font-size: 30px;
    letter-spacing: 17px;
    fill: var(--accent);
  }
  .brand-name {
    position: absolute;
    left: 0;
    right: 0;
    top: 392px;
    margin: 0;
    text-align: center;
    font-family: "Oswald", sans-serif;
    font-weight: 600;
    color: var(--ink-dark);
    text-transform: uppercase;
  }
  .brand-name__line {
    display: block;
    font-size: 128px;
    line-height: 134px;
    letter-spacing: 1px;
  }
  .brand-name__line--sub {
    font-size: 52px;
    line-height: 60px;
    letter-spacing: 3px;
    margin-top: 24px;
  }
  .brand-dots {
    position: absolute;
    top: 696px;
    width: 14px;
    height: 14px;
    border: 1.5px solid var(--rule);
    border-radius: 50%;
    box-sizing: border-box;
  }
  .brand-dots--left { left: 218px; }
  .brand-dots--right { right: 218px; }
  .spec-row {
    position: absolute;
    left: 40px;
    right: 40px;
    top: 906px;
    height: 110px;
    display: flex;
    align-items: center;
    font-family: "Oswald", sans-serif;
    font-weight: 600;
    color: var(--ink-dark);
  }
  .spec {
    font-size: 38px;
    white-space: nowrap;
  }
  .spec small {
    font-size: 14px;
    letter-spacing: 1px;
    margin-left: 2px;
  }
  .spec-rules {
    flex: 1;
    height: 24px;
    margin: 0 18px;
    background:
      linear-gradient(var(--rule), var(--rule)) 0 2px / 100% 1px no-repeat,
      linear-gradient(var(--rule), var(--rule)) 0 8px / 100% 1px no-repeat,
      linear-gradient(var(--rule), var(--rule)) 0 14px / 100% 1px no-repeat,
      linear-gradient(var(--rule), var(--rule)) 0 20px / 100% 1px no-repeat;
  }
  .type-badge {
    width: 104px;
    height: 104px;
    border: 2px solid var(--accent);
    border-radius: 50%;
    display: flex;
    align-items: center;
    justify-content: center;
    color: var(--accent);
    font-size: 36px;
    box-sizing: border-box;
  }
</style>
</head>
<body>
  <main class="label">
    <div class="label__frame"></div>

    <div class="botanical botanical--top" role="img" aria-label="Line illustration of a rose on a leafy stem"></div>

    <svg class="arc-tagline" viewBox="0 0 500 120" aria-label="Handcrafted">
      <defs>
        <path id="tagline-arc" d="M 20 115 Q 250 -30 480 115"/>
      </defs>
      <text><textPath href="#tagline-arc" startOffset="50%" text-anchor="middle">HANDCRAFTED</textPath></text>
    </svg>

    <h1 class="brand-name">
      <span class="brand-name__line">Hollow</span>
      <span class="brand-name__line">Marigold</span>
      <span class="brand-name__line brand-name__line--sub">Distillery</span>
    </h1>
    <span class="brand-dots brand-dots--left"></span>
    <span class="brand-dots brand-dots--right"></span>

    <div class="botanical botanical--bottom" role="img" aria-label="Line illustration of a rose on a leafy stem, mirrored"></div>

    <div class="spec-row">
      <span class="spec spec--abv">40%<small>VOL</small></span>
      <span class="spec-rules"></span>
      <span class="type-badge">GIN</span>
      <span class="spec-rules"></span>
      <span class="spec spec--volume">700<small>ML</small></span>
    </div>
  </main>
</body>
</html>
```